Opening a Hair Salon

Looking for a design for my sign that looks high end, an emphasis on color but welcoming to men and women.

The name is Corvane Haircuts and Colors

Trying capture a more affluent client. Looking for a very modern look.

Reason: Time is going to quick and would like to see a few more options.

```html
<!DOCTYPE html>
<html lang="en">
<head>
<meta charset="UTF-8">
<title>Corvane Haircuts and Colors – Storefront Sign</title>
<link rel="stylesheet" href="https://fonts.googleapis.com/css2?family=Questrial&family=Oswald:wght@500&display=swap">
<style>
  :root {
    --page-bg: #e9e9ec;
    --frame: #0b1022;
    --navy-deep: #0c1a52;
    --navy: #1a2f80;
    --navy-light: #3e54a6;
    --glow: #f4f6fb;
    --white: #ffffff;
    --accent-yellow: #f4ee2a;
    --pill-black: #111111;
    --photo-hair: #8a4f2a;
    --photo-skin: #d9a98a;
    --photo-shirt: #4f7fb8;
  }
  * { box-sizing: border-box; margin: 0; padding: 0; }
  html, body {
    width: 1200px; height: 900px; overflow: hidden;
    background: var(--page-bg);
  }
  .canvas {
    width: 1200px; height: 900px;
    display: flex; align-items: center; justify-content: center;
  }
  .sign {
    position: relative;
    width: 1100px; height: 360px;
    border: 14px solid var(--frame);
    background:
      radial-gradient(ellipse 420px 300px at 80% 45%, var(--glow) 0%, rgba(200,210,235,0.85) 35%, rgba(62,84,166,0) 75%),
      linear-gradient(90deg, var(--navy-deep) 0%, var(--navy) 45%, var(--navy-light) 70%, var(--navy) 100%);
    overflow: hidden;
  }
  .brand {
    position: absolute; left: 44px; top: 108px;
    display: flex; flex-direction: column;
  }
  .brand-name {
    display: flex; align-items: center; gap: 14px;
    font-family: "Questrial", sans-serif;
    font-size: 72px; line-height: 1;
    color: var(--white);
  }
  .brand-mark {
    width: 20px; height: 20px; border-radius: 50%;
    background: var(--white);
  }
  .brand-tagline {
    margin-top: 20px; margin-left: 34px;
    font-family: "Questrial", sans-serif;
    font-size: 24px; letter-spacing: 1px; line-height: 1;
    color: var(--accent-yellow);
  }
  .accent-line {
    position: absolute; left: 78px; top: 250px;
    width: 520px; height: 6px;
    background: var(--accent-yellow);
  }
  .phone-pill {
    position: absolute; left: 382px; top: 96px;
    display: flex; align-items: center; gap: 10px;
    padding: 7px 20px 7px 10px;
    background: var(--pill-black);
    border: 3px solid var(--white);
    border-radius: 40px;
    font-family: "Oswald", sans-serif; font-weight: 500;
    font-size: 34px; color: var(--white); line-height: 1;
    z-index: 2;
  }
  .phone-icon { width: 34px; height: 34px; }
  .salon-photo {
    position: absolute; right: 0; top: 0;
    width: 440px; height: 100%;
    background:
      linear-gradient(110deg,
        rgba(0,0,0,0) 0%,
        var(--photo-hair) 12%, var(--photo-skin) 28%, var(--photo-hair) 42%,
        #5a3a28 58%, var(--photo-skin) 72%, var(--photo-shirt) 90%);
    opacity: 0.9;
    -webkit-mask-image: linear-gradient(90deg, transparent 0%, #000 18%);
            mask-image: linear-gradient(90deg, transparent 0%, #000 18%);
  }
</style>
</head>
<body>
<main class="canvas">
  <section class="sign" aria-label="Corvane Haircuts and Colors storefront sign">
    <div class="brand">
      <div class="brand-name"><span class="brand-mark" aria-hidden="true"></span>Corvane</div>
      <div class="brand-tagline">HAIRCUTS &amp; COLORS</div>
    </div>
    <div class="accent-line" aria-hidden="true"></div>
    <div class="phone-pill">
      <svg class="phone-icon" viewBox="0 0 40 40" aria-hidden="true">
        <circle cx="20" cy="20" r="18" fill="none" stroke="#fff" stroke-width="2.5"/>
        <path d="M14 11c1-1 2.5-1 3.2.3l1.8 3.2c.5.9.2 1.8-.5 2.4l-1.2 1c.9 2 2.6 3.8 4.6 4.7l1-1.2c.6-.7 1.6-.9 2.4-.4l3.2 1.8c1.2.7 1.3 2.2.3 3.2l-1.6 1.6c-1.3 1.3-3.2 1.6-4.9.8-4.6-2.2-8.3-5.9-10.5-10.5-.8-1.7-.5-3.6.8-4.9z" fill="#fff"/>
      </svg>
      <span class="phone-number">2468 1357</span>
    </div>
    <div class="salon-photo" role="img" aria-label="Photo of a woman with long glossy brown hair and a man with styled dark hair in a blue shirt"></div>
  </section>
</main>
</body>
</html>
```